Amber Fox Quest "Your path, my quest"

Individual coaching: life coach & projec Amberfox (amber fox) represents the flight, freedom to be happy. The mission: to be well in his mission in life. sober and soft design which refers professionalism, safety, wellness, balance, personal development. my coordinates = Marta Kovin Life & Project 0462 coach / 31.78.25 marta@amberfoxquest.be

Reason: Business card that refers to the professional (life coaching) and sweetness / freedom of achievement.

Target Market(s)

adults in search of well being, balance for themselves and / or their children

Contact Information for Business Card

Marta Kovin
Life & project coach
0462/31.78.25
marta@amberfoxquest.be

Requirements
Must have
• AMBER FOX QUEST logo tag "Your flight, my mission"
Nice to have
• originality pure appearance, gentle and professional
Should not have
• overdoing banking organization

```html
<!DOCTYPE html>
<html lang="en">
<head>
<meta charset="utf-8">
<title>Amber Fox Quest – Business Card</title>
<link rel="stylesheet" href="https://fonts.googleapis.com/css2?family=Open+Sans:wght@400;700;800&family=Crimson+Text:wght@700&display=swap">
<style>
  :root {
    --stage: #2b2b2d;
    --card-white: #ffffff;
    --sky-deep: #0a3fb8;
    --sky-mid: #1f7ae0;
    --sky-light: #bfe6ff;
    --brand-blue: #1a8ccc;
    --navy: #233a6b;
    --ink: #3a3f4a;
    --divider: #7a7f88;
    --white: #ffffff;
  }
  * { box-sizing: border-box; margin: 0; padding: 0; }
  html, body {
    width: 1200px; height: 960px; overflow: hidden;
    background: var(--stage);
    font-family: "Open Sans", Arial, sans-serif;
  }
  .card {
    position: absolute;
    width: 620px; height: 372px;
    border-radius: 4px;
    overflow: hidden;
    box-shadow: 0 10px 30px rgba(0,0,0,.45);
  }
  /* Front */
  .card--front { left: 80px; top: 80px; }
  .front__sky {
    position: absolute; inset: 0;
    background:
      radial-gradient(ellipse 45% 55% at 42% 52%, var(--sky-light) 0%, rgba(120,200,255,.6) 35%, rgba(31,122,224,0) 75%),
      linear-gradient(160deg, var(--sky-deep) 0%, var(--sky-mid) 55%, #3a9ef0 100%);
  }
  .front__brand {
    position: absolute; left: 0; right: 0; top: 130px;
    text-align: center; color: var(--white);
  }
  .front__name {
    font-weight: 800; font-size: 50px; letter-spacing: .5px; line-height: 1.1;
  }
  .front__tagline {
    margin-top: 14px;
    font-weight: 700; font-size: 24px;
  }
  /* Back */
  .card--back { left: 500px; top: 508px; background: var(--card-white); }
  .back__brand {
    position: absolute; left: 30px; top: 168px; width: 300px;
    display: flex; align-items: center; gap: 10px;
  }
  .back__dot {
    width: 12px; height: 12px; border-radius: 50%;
    background: var(--brand-blue); flex: none;
  }
  .back__name-logo {
    font-weight: 800; font-size: 30px; color: var(--brand-blue); line-height: 1;
    white-space: nowrap;
  }
  .back__divider {
    position: absolute; left: 345px; top: 40px; width: 1px; height: 292px;
    background: var(--divider);
  }
  .person { position: absolute; left: 366px; top: 52px; }
  .person__name { font-weight: 700; font-size: 28px; color: var(--navy); line-height: 1.1; }
  .person__role {
    font-family: "Crimson Text", Georgia, serif;
    font-weight: 700; font-size: 17px; color: var(--brand-blue);
  }
  .contact {
    position: absolute; left: 366px; top: 222px; right: 16px;
    list-style: none;
  }
  .contact__item {
    display: flex; align-items: center; gap: 10px;
    font-size: 16px; color: var(--ink); line-height: 28px;
    white-space: nowrap;
  }
  .contact__icon {
    width: 18px; height: 18px; flex: none;
  }
</style>
</head>
<body>
  <section class="card card--front">
    <div class="front__sky" role="img" aria-label="Bright blue sky with sunburst, soft clouds and a flock of white birds in flight"></div>
    <div class="front__brand">
      <div class="front__name">Amber Fox Quest</div>
      <div class="front__tagline">Votre chemin, ma quête</div>
    </div>
  </section>

  <section class="card card--back">
    <div class="back__brand">
      <span class="back__dot"></span>
      <span class="back__name-logo">Amber Fox Quest</span>
    </div>
    <div class="back__divider"></div>
    <div class="person">
      <div class="person__name">Marta Kovin</div>
      <div class="person__role">Life &amp; project coaching</div>
    </div>
    <ul class="contact">
      <li class="contact__item">
        <svg class="contact__icon" viewBox="0 0 18 18" aria-hidden="true">
          <rect width="18" height="18" rx="2" fill="var(--navy)"/>
          <path d="M5 4c1 0 2 2 2 3s-1 1-1 1c.5 1.5 1.5 2.5 3 3 0 0 0-1 1-1s3 1 3 2-1 2-2 2C7 14 4 11 4 6c0-1 0-2 1-2z" fill="var(--white)"/>
        </svg>
        0462/31.78.25
      </li>
      <li class="contact__item">
        <svg class="contact__icon" viewBox="0 0 18 18" aria-hidden="true">
          <rect width="18" height="18" rx="2" fill="var(--navy)"/>
          <rect x="3.5" y="5" width="11" height="8" fill="none" stroke="var(--white)" stroke-width="1.4"/>
          <path d="M3.5 5l5.5 4.5L14.5 5" fill="none" stroke="var(--white)" stroke-width="1.4"/>
        </svg>
        marta@amberfoxquest.be
      </li>
      <li class="contact__item">
        <svg class="contact__icon" viewBox="0 0 18 18" aria-hidden="true">
          <rect width="18" height="18" rx="2" fill="var(--navy)"/>
          <circle cx="9" cy="9" r="5" fill="none" stroke="var(--white)" stroke-width="1.3"/>
          <path d="M4 9h10M9 4c-2.5 2.5-2.5 7.5 0 10M9 4c2.5 2.5 2.5 7.5 0 10" fill="none" stroke="var(--white)" stroke-width="1"/>
        </svg>
        www.amberfoxquest.be
      </li>
    </ul>
  </section>
</body>
</html>
```